Private Dining Restaurant Menu Design

Looking for help in designing a private dining room menu brochure - probably would need 4 panel layout to make all of the content fit, or a 5.5x8" booklet. Open to your ideas on layout/vessel - would want to post on website and be able to print to hand out to guests interested in booking our private dining room.

All content is in the attached "Private Dining Menu".

Would like to match existing dinner menu design - also attached.

Website is www.copperkettlebistro.com

Requirements
Must have
• Easy to read format of a brochure of the private dining menu content - want to be able to hand out to interested guests and have it simple and easy to read/flip through.

```html
<!DOCTYPE html>
<html lang="en">
<head>
<meta charset="utf-8">
<title>Copper Kettle Bistro – Private Dining Menu</title>
<link href="https://fonts.googleapis.com/css2?family=Crimson+Pro:wght@600;700&family=Merriweather:ital,wght@1,400;1,700&family=Roboto:ital,wght@0,400;0,500;0,700;1,400&display=swap" rel="stylesheet">
<style>
  :root {
    --navy: #1b2b5e;
    --navy-soft: #223468;
    --brick: #8b2b2b;
    --cream: #ebe6d6;
    --tan: #ddd2bb;
    --paper: #ffffff;
    --ink: #1c1c1c;
    --ink-soft: #333333;
    --dessert-sub: #d6dbe8;
  }
  * { margin: 0; padding: 0; box-sizing: border-box; }
  html, body { width: 825px; height: 1200px; overflow: hidden; background: var(--navy); }
  .menu-page {
    position: relative;
    width: 825px; height: 1200px;
    background: var(--navy);
    font-family: "Roboto", Arial, sans-serif;
    color: var(--ink);
  }
  .section { position: absolute; left: 10px; right: 10px; }
  .appetizers { top: 10px; height: 313px; background: var(--cream); }
  .platters { top: 323px; height: 330px; background: var(--tan); }
  .lower { top: 653px; height: 537px; background: var(--paper); overflow: hidden; }

  .section-title {
    font-family: "Crimson Pro", Georgia, serif;
    font-weight: 700;
    color: var(--brick);
    font-size: 23px;
    letter-spacing: 0.2px;
    text-transform: uppercase;
    white-space: nowrap;
  }
  .section-title .note {
    font-family: "Roboto", Arial, sans-serif;
    text-transform: none;
    font-weight: 400;
    font-size: 12px;
    margin-left: 8px;
    letter-spacing: 0;
  }
  .section-title .note b { font-style: italic; font-weight: 700; }

  .appetizers .section-title { position: absolute; left: 52px; top: 34px; }
  .platters .section-title { position: absolute; left: 52px; top: 40px; }

  .item-list { position: absolute; list-style: none; }
  .appetizers .item-list { left: 73px; right: 52px; top: 76px; }
  .platters .item-list { left: 73px; right: 52px; top: 110px; }
  .item {
    display: flex; align-items: baseline;
    height: 37.6px;
    font-size: 15px; font-weight: 700; color: var(--ink);
  }
  .platters .item { height: 37.7px; }
  .leader {
    flex: 1; height: 3px; margin: 0 4px;
    background-image: radial-gradient(circle, var(--navy) 1.1px, transparent 1.3px);
    background-size: 5px 3px;
    background-repeat: repeat-x;
  }
  .price {
    font-family: "Merriweather", Georgia, serif;
    font-style: italic;
    font-size: 12.5px;
    color: var(--brick);
    width: 32px;
    text-align: right;
  }
  .platters .price { width: 72px; }
  .platters .price.small { width: 48px; text-align: left; margin-left: 18px; }
  .platters .leader { margin-right: 0; }
  .size-heads {
    position: absolute; top: 80px; right: 52px;
    display: flex;
    font-family: "Merriweather", Georgia, serif;
    font-style: italic; font-weight: 700;
    font-size: 13px; color: var(--brick);
  }
  .size-heads span:first-child { margin-right: 32px; }

  .bg-rings {
    position: absolute; left: 0; top: 10px; width: 230px; height: 330px;
    background: radial-gradient(ellipse at 30% 40%, rgba(200,190,165,0.18), rgba(255,255,255,0) 70%);
  }
  .bg-rings.right { left: 560px; top: -20px; width: 260px; height: 150px; }

  .beverages { position: absolute; left: 52px; top: 30px; width: 330px; }
  .beverages .section-title { margin-bottom: 10px; }
  .beverage-intro {
    margin-left: 21px;
    font-style: italic; font-size: 15px; line-height: 23px;
    text-align: justify; color: var(--ink-soft);
    margin-bottom: 16px;
  }
  .option-list { margin-left: 21px; list-style: none; }
  .option-name { font-size: 15px; font-weight: 700; line-height: 20px; }
  .option-desc {
    margin-left: 14px; margin-bottom: 5px;
    font-size: 15px; line-height: 23px; text-align: justify; color: var(--ink-soft);
  }

  .dessert-card {
    position: absolute; left: 445px; top: 31px; width: 320px; height: 478px;
    background: var(--navy-soft);
    border-radius: 10px;
    box-shadow: 0 2px 6px rgba(0,0,0,0.35);
    color: var(--paper);
    text-align: center;
    overflow: hidden;
  }
  .dessert-card .card-title {
    margin-top: 46px;
    font-family: "Crimson Pro", Georgia, serif;
    font-weight: 700; font-size: 23px; text-transform: uppercase;
    letter-spacing: 0.2px;
  }
  .dessert-card .card-note { font-size: 11px; margin-top: 2px; }
  .dessert { margin-top: 28px; position: relative; z-index: 1; }
  .dessert + .dessert { margin-top: 26px; }
  .dessert-name { font-size: 15px; font-weight: 700; line-height: 24px; }
  .dessert-sub { font-size: 15px; line-height: 24px; color: var(--dessert-sub); }
  .dessert-price {
    font-family: "Merriweather", Georgia, serif;
    font-style: italic; font-weight: 700; font-size: 16px; line-height: 28px;
  }
  .dessert-price .detail { font-weight: 400; }
  .treeline {
    position: absolute; left: 0; right: 0; bottom: 0; height: 140px;
    background: linear-gradient(to bottom, rgba(110,125,165,0) 0%, rgba(110,125,165,0.45) 100%);
  }
</style>
</head>
<body>
<main class="menu-page">
  <section class="section appetizers">
    <h2 class="section-title">Appetizers<span class="note">(price is by the dozen)</span></h2>
    <ul class="item-list">
      <li class="item">Texas Egg Rolls<span class="leader"></span><span class="price">$25</span></li>
      <li class="item">Chicken Wings (Buffalo, BBQ, OR Blackened)<span class="leader"></span><span class="price">$12</span></li>
      <li class="item">Baby Back Ribs<span class="leader"></span><span class="price">$30</span></li>
      <li class="item">Sliders (Pulled Pork or Rotisserie Chicken)<span class="leader"></span><span class="price">$35</span></li>
      <li class="item">Wood-Roasted Quesadillas<span class="leader"></span><span class="price">$30</span></li>
      <li class="item">Kettle Skins<span class="leader"></span><span class="price">$25</span></li>
    </ul>
  </section>

  <section class="section platters">
    <h2 class="section-title">Platters – Small &amp; Large<span class="note">(small <b>serves:10-15</b> &nbsp;/&nbsp; large <b>serves: 25-30</b>)</span></h2>
    <div class="size-heads"><span>Small</span><span>Large</span></div>
    <ul class="item-list">
      <li class="item">Chips, Salsa, and Guacamole<span class="leader"></span><span class="price small">$25</span><span class="price">$45</span></li>
      <li class="item">Fresh Fruit Platter<span class="leader"></span><span class="price small">$50</span><span class="price">$75</span></li>
      <li class="item">Hot Artichoke Dip (comes with bread and tortilla chips)<span class="leader"></span><span class="price small">$30</span><span class="price">$60</span></li>
      <li class="item">Domestic Cheese and Crackers<span class="leader"></span><span class="price small">$45</span><span class="price">$65</span></li>
      <li class="item">Fresh Veggie Platter<span class="leader"></span><span class="price small">$40</span><span class="price">$65</span></li>
    </ul>
  </section>

  <section class="section lower">
    <div class="bg-rings" role="img" aria-label="Faint wood tree-ring texture"></div>
    <div class="bg-rings right" role="img" aria-label="Faint wood tree-ring texture"></div>

    <div class="beverages">
      <h2 class="section-title">Beverage Options</h2>
      <p class="beverage-intro">We offer a full bar with a variety of NA, liquor, beer, and wine options All beverages will be charged per menu price</p>
      <dl class="option-list">
        <dt class="option-name">NA Beverage Host</dt>
        <dd class="option-desc">Soda, Iced Tea, Lemonade, Coffee, and Hot Tea hosted by renter for their guests</dd>
        <dt class="option-name">Full Host</dt>
        <dd class="option-desc">All NA and Alcoholic beverages to be hosted by the renter for their guests</dd>
        <dt class="option-name">Partial Host</dt>
        <dd class="option-desc">A set amount or certain types of beverages hosted by the renter for their guests</dd>
        <dt class="option-name">Cash Bar</dt>
        <dd class="option-desc">Each beverage will be paid for by each individual guest</dd>
      </dl>
    </div>

    <aside class="dessert-card">
      <div class="treeline" role="img" aria-label="Soft silhouette of pine trees along the bottom"></div>
      <h2 class="card-title">Dessert Options</h2>
      <p class="card-note">(price is per item)</p>
      <div class="dessert">
        <p class="dessert-name">House Made Cheesecake Slice</p>
        <p class="dessert-sub">(turtle, strawberry, or plain)</p>
        <p class="dessert-price">$5 /slice</p>
      </div>
      <div class="dessert">
        <p class="dessert-name">Whole House Made Cheesecake</p>
        <p class="dessert-sub">(turtle, strawberry, or plain)</p>
        <p class="dessert-price">$60 <span class="detail">(15 slices at $4 /slice)</span></p>
      </div>
      <div class="dessert">
        <p class="dessert-name">Assorted Bars and Cookie Platter</p>
        <p class="dessert-sub">(25 bars/cookies)</p>
        <p class="dessert-price">$25</p>
      </div>
    </aside>
  </section>
</main>
</body>
</html>
```